DESIGN OF STATIONERY - TORVALE MED

WE WORK IN THE FIELD OF HEALTH (IMAGING: MRI - CT ETC.).
WE WOULD LIKE TO CREATE THE ENTIRE STATIONERY DESIGN : LETTERHEAD, BUSINESS CARD, CALENDAR, INVOICES, CD HOLDER, ETC.

Target Market(s)

PERSONS UNDERTAKING HEALTH EXAMINATIONS

```html
<!DOCTYPE html>
<html lang="en">
<head>
<meta charset="utf-8">
<title>Torvale Med – Business Card</title>
<link rel="stylesheet" href="https://fonts.googleapis.com/css2?family=Montserrat:wght@400;500;600;700&display=swap">
<style>
  :root {
    --page-bg: #ecebe8;
    --brand-blue: #1b6bb3;
    --brand-blue-emboss: #4f8fcc;
    --brand-teal: #17a08c;
    --card-white: #f7f7f7;
    --text-grey: #454545;
    --shadow: rgba(0, 0, 0, 0.14);
  }
  * { box-sizing: border-box; margin: 0; padding: 0; }
  html, body {
    width: 1200px;
    height: 960px;
    overflow: hidden;
    background: var(--page-bg);
    font-family: "Montserrat", sans-serif;
  }
  .canvas {
    width: 1200px;
    height: 960px;
    display: flex;
    flex-direction: column;
    align-items: center;
    justify-content: center;
    gap: 60px;
  }
  .card {
    width: 630px;
    height: 360px;
    border-radius: 4px;
    box-shadow: 0 10px 28px var(--shadow);
    position: relative;
  }
  .card--front {
    background: var(--brand-blue);
    display: flex;
    align-items: center;
    justify-content: center;
  }
  .front-lockup { text-align: left; }
  .front-lockup .brand-name {
    color: var(--brand-blue-emboss);
    font-size: 58px;
  }
  .front-lockup .brand-tagline {
    color: var(--brand-blue-emboss);
    font-size: 20px;
  }
  .brand-name {
    font-weight: 700;
    letter-spacing: 1px;
    line-height: 1;
    display: flex;
    align-items: center;
    gap: 12px;
  }
  .brand-dot {
    width: 14px;
    height: 14px;
    border-radius: 50%;
    background: currentColor;
    flex: none;
  }
  .brand-tagline {
    font-weight: 600;
    margin-top: 8px;
    padding-left: 26px;
  }
  .card--back {
    background: var(--card-white);
    display: flex;
    align-items: center;
    padding: 0 40px 0 44px;
  }
  .back-lockup { width: 270px; }
  .back-lockup .brand-name {
    color: var(--brand-blue);
    font-size: 30px;
    gap: 8px;
  }
  .back-lockup .brand-dot { width: 9px; height: 9px; }
  .back-lockup .brand-tagline {
    color: var(--brand-teal);
    font-size: 12px;
    margin-top: 5px;
    padding-left: 17px;
  }
  .divider {
    width: 2px;
    height: 210px;
    background: var(--brand-blue);
    margin: 0 26px 0 10px;
    flex: none;
  }
  .details { color: var(--text-grey); }
  .person-name {
    color: var(--brand-blue);
    font-weight: 700;
    font-size: 20px;
    letter-spacing: 0.5px;
  }
  .person-role {
    color: var(--brand-teal);
    font-weight: 600;
    font-size: 16px;
    margin-bottom: 14px;
  }
  .address {
    font-style: normal;
    font-size: 14px;
    line-height: 1.4;
    margin-bottom: 12px;
  }
  .contact-list { list-style: none; font-size: 14px; line-height: 1.5; }
  .contact-list li { display: flex; align-items: center; gap: 8px; }
  .contact-icon { width: 13px; height: 13px; flex: none; fill: var(--brand-teal); }
</style>
</head>
<body>
<main class="canvas">

  <section class="card card--front" aria-label="Business card front">
    <div class="front-lockup">
      <div class="brand-name"><span class="brand-dot"></span>TORVALE MED</div>
      <div class="brand-tagline">Health Care Diagnostic</div>
    </div>
  </section>

  <section class="card card--back" aria-label="Business card back">
    <div class="back-lockup">
      <div class="brand-name"><span class="brand-dot"></span>TORVALE MED</div>
      <div class="brand-tagline">Health Care Diagnostic</div>
    </div>
    <div class="divider"></div>
    <div class="details">
      <p class="person-name">JONAS L. FERRAND</p>
      <p class="person-role">Managing Director</p>
      <address class="address">
        Torvale-Med-R<br>
        2nd Floor 18 Caldmoor<br>
        Square Glasgow G3 7RT
      </address>
      <ul class="contact-list">
        <li>
          <svg class="contact-icon" viewBox="0 0 16 16" aria-hidden="true"><path d="M3.6 1.2l2.2 2.6-1.3 1.8c.9 2 2.4 3.5 4.4 4.4l1.8-1.3 2.6 2.2-1.1 2.2c-5.6-.3-10-4.7-10.3-10.3z"/></svg>
          07400 512 386
        </li>
        <li>
          <svg class="contact-icon" viewBox="0 0 16 16" aria-hidden="true"><path d="M1 3h14v1.2L8 8.6 1 4.2zM1 5.8l7 4.4 7-4.4V13H1z"/></svg>
          info@torvalemed.com
        </li>
        <li>
          <svg class="contact-icon" viewBox="0 0 16 16" aria-hidden="true"><circle cx="8" cy="8" r="7"/><path d="M1 8h14M8 1c2.5 2.2 2.5 11.8 0 14M8 1c-2.5 2.2-2.5 11.8 0 14" stroke="#f7f7f7" stroke-width="1.1" fill="none"/></svg>
          www.torvalemed.com
        </li>
      </ul>
    </div>
  </section>

</main>
</body>
</html>
```